Verodex business card

Business card for sustainable investment company called "Verodex". Verodex is an exchange platform selling carbon credits between buyers and sellers. Carbon Credits are an environmental commodity for reducing global carbon emissions.

the card should obviously have our logo and the theme should be sustainability/environment mixed with a trading platform.

Contact Information for Business Card

Logo, Name, Title, Phone, Email

Colors
0054AA
0677BA
7BADD7
CADEEF
E8F1F8
0094D4
00A9DD
6FCCEA
C7EBF8
E9F6FB
00AB8E
00BBA5
67D7C9
C6EFE9
E9F9F6
59FF00
82FF00
B8FF75
E3FFCB
F4FFEA

```html
<!DOCTYPE html>
<html lang="en">
<head>
<meta charset="utf-8">
<title>Verodex business card</title>
<link rel="stylesheet" href="https://fonts.googleapis.com/css2?family=Montserrat:wght@400;500;700&display=swap">
<style>
  :root {
    --bg: #3b3c3e;
    --navy: #162a52;
    --paper: #ffffff;
    --accent: #3a8fd0;
    --accent-soft: #4a9ad6;
    --back-mark: #3f7fbf;
  }
  * { margin: 0; padding: 0; box-sizing: border-box; }
  html, body {
    width: 1200px; height: 1059px; overflow: hidden;
    background: var(--bg);
    font-family: "Montserrat", sans-serif;
  }
  .stage { position: relative; width: 1200px; height: 1059px; }
  .card {
    position: absolute; left: 256px; width: 688px; height: 391px;
    border-radius: 24px; overflow: hidden;
  }
  .card-front { top: 100px; background: var(--paper); }
  .card-back { top: 538px; background: var(--navy); }

  .brand {
    position: absolute; left: 0; right: 0; top: 82px;
    display: flex; align-items: center; justify-content: center; gap: 14px;
  }
  .brand-square { width: 30px; height: 30px; background: var(--accent); border-radius: 4px; }
  .brand-name {
    font-weight: 700; font-size: 46px; letter-spacing: 1px;
    color: var(--navy); text-transform: uppercase; line-height: 1;
  }

  .person {
    position: absolute; right: 372px; top: 206px; text-align: right; color: var(--navy);
  }
  .person-name { font-weight: 700; font-size: 27px; letter-spacing: 1.5px; line-height: 1.1; text-transform: uppercase; }
  .person-title { font-weight: 400; font-size: 18px; letter-spacing: 1px; line-height: 1.2; text-transform: uppercase; }

  .divider {
    position: absolute; left: 344px; top: 198px; width: 2px; height: 68px; background: var(--accent);
  }

  .contacts {
    position: absolute; left: 373px; top: 193px; list-style: none;
  }
  .contacts li {
    display: flex; align-items: center; gap: 8px;
    font-size: 16px; color: var(--navy); height: 26.5px; letter-spacing: 0.5px;
  }
  .contacts svg { width: 13px; height: 13px; flex: none; }

  .address-band {
    position: absolute; left: 0; right: 0; top: 313px; height: 24px;
    background: var(--navy); color: var(--paper);
    font-size: 16px; letter-spacing: 0.6px;
    display: flex; align-items: center; justify-content: center;
  }

  .back-brand {
    position: absolute; left: 0; right: 0; top: 0; bottom: 0;
    display: flex; align-items: center; justify-content: center;
  }
  .back-brand .brand-name { font-size: 60px; color: var(--back-mark); }
</style>
</head>
<body>
<main class="stage">
  <section class="card card-front">
    <div class="brand">
      <span class="brand-square"></span>
      <span class="brand-name">Verodex</span>
    </div>

    <div class="person">
      <p class="person-name">Dana Whitford</p>
      <p class="person-title">Manager</p>
    </div>

    <span class="divider"></span>

    <ul class="contacts">
      <li>
        <svg viewBox="0 0 16 16" aria-hidden="true"><path fill="var(--accent-soft)" d="M3.6 1.5l2.2 2.6-1.3 1.7c.8 2 2.4 3.6 4.4 4.5l1.6-1.3 2.7 2.2-1.5 2.3C6.6 13.4 2.3 9.1 1.5 3.2z"/></svg>
        <span>555-318-2047</span>
      </li>
      <li>
        <svg viewBox="0 0 16 16" aria-hidden="true"><rect x="1" y="3" width="14" height="10" rx="1" fill="var(--accent-soft)"/><path d="M1.5 4l6.5 5 6.5-5" fill="none" stroke="#fff" stroke-width="1.3"/></svg>
        <span>hello@verodex-mail.com</span>
      </li>
      <li>
        <svg viewBox="0 0 16 16" aria-hidden="true"><g fill="none" stroke="var(--accent-soft)" stroke-width="1.2"><circle cx="8" cy="8" r="6.5"/><ellipse cx="8" cy="8" rx="3" ry="6.5"/><path d="M1.5 8h13M2.5 4.8h11M2.5 11.2h11"/></g></svg>
        <span>www.verodex-site.com</span>
      </li>
    </ul>

    <div class="address-band">2715 Harbor Lane, Suite 4 Brookfield, WI 53045</div>
  </section>

  <section class="card card-back">
    <div class="back-brand">
      <span class="brand-name">Verodex</span>
    </div>
  </section>
</main>
</body>
</html>
```